'Horizons on Common Ground'

We are after a flyer to sell a two day conference to sponsors, delegates and other Councils to participate.
The conference aims to be a forum for Northern Territory Councils to get together and discuss ideas, issues and overcome challenges and isolation in collaboration.
The conference will be a inaugural event with the plan to host a annual two day conference each year with a specific theme relevant to all Northern Territory Councils. - Give the Councils a voice.

```html
<!DOCTYPE html>
<html lang="en">
<head>
<meta charset="utf-8">
<title>Horizons on Common Ground – Flyer</title>
<link rel="stylesheet" href="https://fonts.googleapis.com/css2?family=Questrial&family=Arimo:ital,wght@0,400;0,700;1,400;1,700&display=swap">
<style>
  :root {
    --page: #eef1f3;
    --sea-deep: #1d4d66;
    --sea-mid: #3f7f9c;
    --sky: #9ccbe0;
    --sky-light: #d6ebf3;
    --band: #8a979d;
    --paper: #ffffff;
    --ink: #1b1b1b;
    --white: #ffffff;
    --grid: rgba(255,255,255,0.28);
  }
  * { box-sizing: border-box; margin: 0; padding: 0; }
  html, body { width: 1200px; height: 523px; overflow: hidden; background: var(--page); }
  .canvas { position: relative; width: 1200px; height: 523px; }
  .flyer {
    position: absolute; left: 434px; top: 14px; width: 332px; height: 495px;
    background: var(--paper); overflow: hidden;
    box-shadow: 0 2px 10px rgba(0,0,0,0.18);
  }
  .hero {
    position: absolute; left: 0; top: 0; width: 332px; height: 397px;
    background: linear-gradient(180deg, var(--sky-light) 0%, var(--sky) 22%, var(--sea-mid) 50%, var(--sea-deep) 100%);
  }
  .hero-grid {
    position: absolute; inset: 0;
    background-image:
      linear-gradient(var(--grid) 1px, transparent 1px),
      linear-gradient(90deg, var(--grid) 1px, transparent 1px);
    background-size: 55px 60px;
    pointer-events: none;
  }
  .photo { position: absolute; }
  .photo-coast { left: 0; top: 0; width: 108px; height: 37px; background: linear-gradient(180deg, #7fb3d6 0%, #a77a4e 55%, #d9c7a2 100%); }
  .photo-green { left: 0; top: 43px; width: 108px; height: 42px; background: linear-gradient(180deg, #8bc35a 0%, #5f9c3a 60%, #a9c98a 100%); }
  .photo-shore { left: 114px; top: 119px; width: 218px; height: 27px; background: linear-gradient(180deg, #c7dff0 0%, #3d6b3c 45%, #e4d6b5 75%, #7fb2c8 100%); }
  .logo-strip {
    position: absolute; left: 114px; top: 150px; width: 218px; height: 39px;
    background: linear-gradient(90deg, #e7d7dd 0%, #c9b6c4 60%, #8d8a96 100%);
    display: flex; align-items: center; gap: 5px; padding-left: 6px;
  }
  .logo-mark { width: 9px; height: 9px; border-radius: 50%; background: var(--sea-deep); }
  .logo-name { font-family: "Arimo", sans-serif; font-weight: 700; font-size: 7px; color: var(--sea-deep); letter-spacing: 0.3px; }
  .values {
    position: absolute; left: 6px; top: 196px; width: 200px;
    font-family: "Arimo", sans-serif; font-style: italic; color: var(--white);
  }
  .values h3 { font-family: "Questrial", sans-serif; font-style: normal; font-weight: 400; font-size: 6.5px; line-height: 7px; letter-spacing: 0.4px; margin-top: 1px; }
  .values p { font-size: 5px; line-height: 6px; opacity: 0.92; }
  .title {
    position: absolute; left: 12px; top: 328px;
    font-family: "Questrial", sans-serif; font-weight: 400; color: var(--white);
    font-size: 21px; line-height: 21px; letter-spacing: 0.6px; text-transform: uppercase;
  }
  .date-band {
    position: absolute; left: 0; top: 377px; width: 332px; height: 20px;
    background: var(--band); color: var(--white);
    font-family: "Questrial", sans-serif; font-size: 13px; line-height: 20px; padding-left: 12px;
  }
  .statement { position: absolute; left: 62px; top: 408px; width: 200px; font-family: "Arimo", sans-serif; color: var(--ink); }
  .statement h2 { font-style: italic; font-weight: 700; font-size: 10px; letter-spacing: 0.2px; }
  .statement p { font-style: italic; font-weight: 700; font-size: 4.6px; line-height: 1.3; text-transform: uppercase; margin: 1px 0 5px; }
</style>
</head>
<body>
<main class="canvas">
  <article class="flyer">
    <section class="hero" role="img" aria-label="Photograph of a calm turquoise bay under a cloudy sky, with a rocky headland along the shore">
      <div class="hero-grid"></div>
    </section>
    <div class="photo photo-coast" role="img" aria-label="Photo of red rock outcrop on a coastal beach"></div>
    <div class="photo photo-green" role="img" aria-label="Aerial photo of green floodplain wetlands"></div>
    <div class="photo photo-shore" role="img" aria-label="Photo of a tree-lined shoreline with sand and shallow water"></div>
    <div class="logo-strip" role="img" aria-label="Photo of pandanus palms silhouetted at dusk with shire name">
      <span class="logo-mark"></span>
      <span class="logo-name">COASTAL PLAINS SHIRE</span>
    </div>

    <section class="values">
      <h3>CORE VALUES</h3>
      <p>We have identified these key values and principles as integral to the achievement of our vision.</p>
      <h3>RESPECT</h3>
      <p>Acknowledge and value individual community culture, Indigenous culture and heritage, in an environment free of discrimination.</p>
      <h3>PROFESSIONALISM</h3>
      <p>Administration, planning, logistics, communication and governance of the highest standard.</p>
      <h3>RESULTS</h3>
      <p>Achievement of agreed service delivery standards.</p>
      <h3>INTEGRITY</h3>
      <p>Dealing honestly and fairly with all stakeholders.</p>
      <h3>INNOVATION</h3>
      <p>Developing new ways of delivering services and timely solutions.</p>
      <h3>ENGAGEMENT</h3>
      <p>Listen effectively to residents and collaborate with stakeholders.</p>
    </section>

    <h1 class="title">Horizons on<br>Common Ground</h1>
    <div class="date-band">13th-14th April 2011</div>

    <section class="statement">
      <h2>VISION &amp; MISSION</h2>
      <p>A region whose people are healthy happy and positive about their future.</p>
      <h2>OBJECTIVE</h2>
      <p>A strong, reliable and responsible shire council that will support the people of Coastal Plains by providing a range of high quality services that lead to community, cultural, economic and environmental wellbeing.</p>
    </section>
  </article>
</main>
</body>
</html>
```